4th Generation Family Business Needs a New Card Design!

We are a family owned 4th Generation company. We are based in the Sydney, Australia area and we are desperately in need of a more modern and classy card. We are monumental masons who design, supply & erect lasting memorials throughout cemeteries in Sydney. Our customers are normally in a period of grieving. I have attached logo files that will need to be implemented on the card. Company was established 1935. Australian Owned and Operated. Card needs to be designed to PIXO.com specification.

Target Market(s)

Our target market is based upon people that a grieving for family members that have passed away. We also deal with alot of companies that own and operate cemeteries.

Industry/Entity Type

Business

Contact Information for Business Card

Simon Harcourt, Operations Manager, 0417293086, simon@harcourtmemorials.com.au
Lewis Harcourt, Director, 0491630572, lewis@harcourtmemorials.com.au
Phone # 02 9561 3048
Website: www.harcourtmemorials.com.au
Address: Suite 17, 8 Palfrey Lane, West Carlow, Sydney NSW 2156

Font styles to use
Serif
Decorative
Script

Requirements
Must have
• Would like to see the logo nicely implemented with a modern design. Embossed lettering would be a nice additive.

```html
<!DOCTYPE html>
<html lang="en">
<head>
<meta charset="utf-8">
<title>Harcourt Memorials – Business Card</title>
<link rel="stylesheet" href="https://fonts.googleapis.com/css2?family=Cinzel:wght@500&family=Arimo:wght@400&display=swap">
<style>
  :root {
    --page: #e9e7e3;
    --card-white: #fbfbfa;
    --band-black: #232224;
    --ink-dark: #3a383a;
    --gold: #e6c73a;
    --text-light: #f2f2f2;
    --shadow: rgba(0, 0, 0, 0.22);
  }
  * { box-sizing: border-box; margin: 0; padding: 0; }
  html, body {
    width: 1200px; height: 858px; overflow: hidden;
    background: var(--page);
  }
  .canvas {
    width: 1200px; height: 858px;
    display: flex; align-items: center; justify-content: center; gap: 48px;
  }
  .card {
    position: relative;
    width: 540px; height: 330px;
    background: var(--card-white);
    box-shadow: 0 10px 28px var(--shadow);
    overflow: hidden;
  }

  /* Front */
  .card-front { display: flex; }
  .front-brand {
    width: 44%; height: 100%;
    display: flex; align-items: center; justify-content: center;
  }
  .front-band {
    position: relative;
    width: 56%; height: 100%;
    background: var(--band-black);
    padding: 30px 26px 28px 26px;
    display: flex; flex-direction: column; justify-content: space-between;
  }
  .brand {
    display: flex; align-items: center; gap: 12px;
    font-family: "Cinzel", Georgia, serif;
    font-weight: 500;
    color: var(--ink-dark);
    text-transform: uppercase;
    line-height: 1.15;
  }
  .brand-mark {
    width: 14px; height: 14px; background: var(--ink-dark); flex: none;
  }
  .brand-front { font-size: 22px; letter-spacing: 2px; }
  .brand-back { font-size: 30px; letter-spacing: 3px; }

  .people {
    text-align: right;
    font-family: "Arimo", Arial, sans-serif;
  }
  .people-names {
    color: var(--text-light); font-size: 17px; white-space: nowrap;
  }
  .people-names .divider { margin: 0 4px; }
  .people-titles {
    color: var(--gold); font-size: 11.5px; margin-top: 3px; white-space: nowrap;
  }
  .people-titles .gap { display: inline-block; width: 16px; }

  .contacts {
    display: flex; gap: 10px;
    font-family: "Arimo", Arial, sans-serif;
    color: var(--text-light); font-size: 11.5px; line-height: 1.45;
  }
  .contact-group { display: flex; gap: 8px; }
  .icon-column {
    display: flex; flex-direction: column; gap: 3px; padding-top: 1px;
  }
  .icon {
    width: 14px; height: 14px; border-radius: 3px;
    background: var(--gold);
    display: flex; align-items: center; justify-content: center;
  }
  .icon svg { width: 10px; height: 10px; }
  .contact-list { list-style: none; }

  /* Back */
  .card-back {
    display: flex; align-items: center; justify-content: center;
  }
</style>
</head>
<body>
<main class="canvas">

  <section class="card card-front" aria-label="Business card front">
    <div class="front-brand">
      <div class="brand brand-front">
        <span class="brand-mark"></span>
        <span>Harcourt<br>Memorials</span>
      </div>
    </div>

    <div class="front-band">
      <div class="people">
        <p class="people-names">Simon Harcourt<span class="divider">|</span>Lewis Harcourt</p>
        <p class="people-titles">Operations Manager<span class="gap"></span>Director</p>
      </div>

      <div class="contacts">
        <div class="contact-group">
          <div class="icon-column">
            <span class="icon"><svg viewBox="0 0 10 10"><rect x="3" y="1" width="4" height="8" rx="0.8" fill="none" stroke="#232224" stroke-width="1"/></svg></span>
            <span class="icon"><svg viewBox="0 0 10 10"><path d="M2 1.5 L3.6 1.5 L4.2 3.4 L3.2 4.2 Q4 6 5.8 6.8 L6.6 5.8 L8.5 6.4 L8.5 8 Q4.5 8.5 2 5.5 Q1.2 3.8 2 1.5Z" fill="#232224"/></svg></span>
            <span class="icon"><svg viewBox="0 0 10 10"><rect x="1" y="2.5" width="8" height="5" fill="none" stroke="#232224" stroke-width="1"/><path d="M1 2.5 L5 5.6 L9 2.5" fill="none" stroke="#232224" stroke-width="1"/></svg></span>
          </div>
          <ul class="contact-list">
            <li>0417293086 / 0491630572</li>
            <li>02 9561 3048</li>
            <li>simon@harcourtmemorials.com.au</li>
            <li>lewis@harcourtmemorials.com.au</li>
          </ul>
        </div>
      </div>

      <div class="contacts">
        <div class="contact-group">
          <div class="icon-column">
            <span class="icon"><svg viewBox="0 0 10 10"><circle cx="5" cy="5" r="3.8" fill="none" stroke="#232224" stroke-width="0.9"/><ellipse cx="5" cy="5" rx="1.6" ry="3.8" fill="none" stroke="#232224" stroke-width="0.8"/><line x1="1.2" y1="5" x2="8.8" y2="5" stroke="#232224" stroke-width="0.8"/></svg></span>
            <span class="icon"><svg viewBox="0 0 10 10"><path d="M5 9.2 L2.4 5.3 A3 3 0 1 1 7.6 5.3 Z" fill="#232224"/><circle cx="5" cy="3.7" r="1.1" fill="#e6c73a"/></svg></span>
          </div>
          <ul class="contact-list">
            <li>www.harcourtmemorials.com.au</li>
            <li>Suite 17, 8 Palfrey Lane, West Carlow,</li>
            <li>Sydney NSW 2156</li>
          </ul>
        </div>
      </div>
    </div>
  </section>

  <section class="card card-back" aria-label="Business card back">
    <div class="brand brand-back">
      <span class="brand-mark"></span>
      <span>Harcourt<br>Memorials</span>
    </div>
  </section>

</main>
</body>
</html>
```